Natural Light/Organic/Documentary Photography Business

I like a simple, approachable, feminine, earthy/organic feel. Earth/neutral tones, nothing too loud or obnoxious. I like the watercolor look. I don't want anything too trendy or something I'll get tired of after a couple months. As far as colors, I am much more a fan of cream/taupe/blue/green...not a fan of pink or purple at all.

Target Market(s)

Weddings & Families

Industry/Entity Type

Wedding Photography

Contact Information for Business Card

website, email, phone number

Font styles to use
Other font styles liked:
• Horizontes, Gotham

Colors

Designer to choose colors to be used in the design.

Requirements
Must have
• Website: www.mirelhatchway.com
• Phone: 418.629.5073
• Email: mirel@mirelhatchway.com
Nice to have
• I like the watercolor look but its not necessary. I like simple/earthy tones. Nothing too loud or distracting. Simple & feminine without being too girly. I like an approachable/soft feel.
• Instagram: www.instagram.com/mirelhatchwayphotography/
Should not have
• NO loud colors or design or pattern. I do not want a photo of a camera or lens or anything cheesy like that.

```html
<!DOCTYPE html>
<html lang="en">
<head>
<meta charset="utf-8">
<title>Mirel Hatchway Photography – Business Card</title>
<link href="https://fonts.googleapis.com/css2?family=Open+Sans:wght@400;600&display=swap" rel="stylesheet">
<style>
  :root {
    --page: #ececec;
    --taupe: #8c8077;
    --white: #ffffff;
  }
  html, body {
    margin: 0;
    padding: 0;
    width: 1200px;
    height: 799px;
    overflow: hidden;
    background: var(--page);
    font-family: "Open Sans", Arial, sans-serif;
  }
  .canvas {
    position: relative;
    width: 1200px;
    height: 799px;
  }
  .card {
    position: absolute;
    left: 313px;
    width: 584px;
    height: 333px;
    background: var(--taupe);
    overflow: hidden;
  }
  .card--front { top: 51px; }
  .card--back  { top: 413px; }

  .front__panel {
    position: absolute;
    inset: 0;
  }
  .brand-mark {
    position: absolute;
    left: 370px;
    top: 152px;
    width: 210px;
    text-align: center;
    color: var(--taupe);
    font-size: 21px;
    font-weight: 400;
    letter-spacing: 0.5px;
  }
  .contact {
    position: absolute;
    left: 36px;
    top: 180px;
    color: var(--white);
  }
  .contact__name {
    margin: 0 0 14px;
    font-size: 20px;
    font-weight: 600;
    line-height: 1.2;
  }
  .contact__list {
    list-style: none;
    margin: 0;
    padding: 0;
    font-size: 14px;
    line-height: 19px;
  }
  .contact__item {
    display: flex;
    align-items: center;
    gap: 7px;
  }
  .contact__icon {
    width: 13px;
    height: 13px;
    flex: none;
  }
  .back__name {
    position: absolute;
    inset: 0;
    display: flex;
    align-items: center;
    justify-content: center;
    color: var(--white);
    font-size: 30px;
    font-weight: 400;
    letter-spacing: 1px;
  }
</style>
</head>
<body>
<div class="canvas">

  <section class="card card--front">
    <svg class="front__panel" width="584" height="333" viewBox="0 0 584 333" aria-hidden="true">
      <circle cx="442" cy="166" r="168" fill="var(--white)"/>
      <rect x="442" y="0" width="142" height="333" fill="var(--white)"/>
    </svg>

    <div class="brand-mark">Mirel Hatchway</div>

    <div class="contact">
      <h1 class="contact__name">Mirel Hatchway</h1>
      <ul class="contact__list">
        <li class="contact__item">
          <svg class="contact__icon" viewBox="0 0 14 14" aria-hidden="true">
            <path d="M1 5 C1 2 4 1.5 7 1.5 S13 2 13 5 L10 5.5 L9.5 4 H4.5 L4 5.5 Z" fill="var(--white)"/>
            <path d="M3 7 H11 L12 12.5 H2 Z" fill="var(--white)"/>
            <circle cx="7" cy="9.5" r="1.5" fill="var(--taupe)"/>
          </svg>
          <span>418.629.5073</span>
        </li>
        <li class="contact__item">
          <svg class="contact__icon" viewBox="0 0 14 14" aria-hidden="true">
            <rect x="1" y="3" width="12" height="8.5" fill="var(--white)"/>
            <path d="M1 3 L7 8 L13 3" fill="none" stroke="var(--taupe)" stroke-width="1"/>
          </svg>
          <span>mirel@mirelhatchway.com</span>
        </li>
        <li class="contact__item">
          <svg class="contact__icon" viewBox="0 0 14 14" aria-hidden="true">
            <circle cx="7" cy="7" r="6" fill="var(--white)"/>
            <path d="M4 4 C6 4 6 6 5 7 S4 9 5 11 M9 3 C8 5 10 6 11 7 M8 10 C9 9 10 10 10.5 11" fill="none" stroke="var(--taupe)" stroke-width="1.2"/>
          </svg>
          <span>www.mirelhatchway.com</span>
        </li>
        <li class="contact__item">
          <svg class="contact__icon" viewBox="0 0 14 14" aria-hidden="true">
            <rect x="1.5" y="1.5" width="11" height="11" rx="2" fill="var(--white)"/>
          </svg>
          <span>mirelhatchwayphotography</span>
        </li>
      </ul>
    </div>
  </section>

  <section class="card card--back">
    <div class="back__name">Mirel Hatchway</div>
  </section>

</div>
</body>
</html>
```